Moxy Fen needs some awesome stationary

Do you have what it takes to get my brand? You either do or you don't, have a crack at a design and you my just win my business.

I don't want to waste your or my time, so put your creative genius on either a business card or envelope.

I however need a package of stationary that follows the same brand. I will message you to complete the remaining should I like your first submission.

Here is what I need, have a go!

Basically I need the following for my small business based in melbourne.
- Letterhead (printer ready and MS Word)
- Business Card
- Compliments Slip
- Envelope
- Proposal Cover Page (MS Word only)
- Presentation Folder
- Marbled Fox Cards
- Student Name Tent
- Index Cards
- Vell-Ka

I am establishing the brand and it must be modern, professional but also relaxed; that is not formal and not corporate. It represents a company are leaders, but small enough to care and operate like a bunch of friends. We are bringing people and conversations back to business, and turfing out all the bureaucracy and crazy and wasteful procedures. Its about "lets talk and figure it out together and find even better ways".

Target Market(s)

Mainly companies that build software products, but Agile practices are used in many other industries (even graphic design projects)

Industry/Entity Type

Information Technology

Font styles to use
Sans Serif

Colors
3176b5
aaaaaa

Requirements
Must have
• I like curves and circles and not boxes or rectangles.
• I want a colour rich design with my brand colours, but it must be balanced.
• I want more modern than traditional, but simple modern
Should not have
• Not corporate
• Please don't waste my time if your not going to think about it.
• Don't mess with my primary logo
• Don't change my colours
• Don't overlay logo on image

```html
<!DOCTYPE html>
<html lang="en">
<head>
<meta charset="utf-8">
<title>Moxy Fen – Business Card</title>
<link rel="stylesheet" href="https://fonts.googleapis.com/css2?family=Open+Sans:wght@400;700&display=swap">
<style>
  :root {
    --brand-blue: #3176b5;
    --card-blue: #2d5aa6;
    --brand-grey: #aaaaaa;
    --stripe-grey: #a9b0bb;
    --paper: #ffffff;
    --backdrop: #e9e6e1;
  }
  * { box-sizing: border-box; margin: 0; padding: 0; }
  html, body {
    width: 1200px; height: 950px; overflow: hidden;
    background: var(--backdrop);
    font-family: "Open Sans", sans-serif;
  }
  .sheet {
    position: relative; width: 1200px; height: 950px;
    display: flex; flex-direction: column; align-items: center;
    justify-content: center; gap: 34px;
  }
  .card {
    position: relative; width: 700px; height: 400px;
    border-radius: 26px; overflow: hidden;
    box-shadow: 0 6px 18px rgba(0,0,0,.18);
  }
  .card-front { background: var(--paper); }
  .card-back { background: var(--card-blue); }

  .front-shapes { position: absolute; inset: 0; width: 100%; height: 100%; }

  .brand {
    position: absolute; left: 40px; top: 170px;
    display: flex; align-items: center; gap: 12px;
    white-space: nowrap;
  }
  .brand-dot {
    width: 34px; height: 34px; border-radius: 50%;
    background: var(--card-blue); flex: none;
  }
  .brand-name {
    font-size: 40px; font-weight: 700; color: var(--card-blue);
    letter-spacing: -0.5px; line-height: 1; white-space: nowrap;
  }

  .holder {
    position: absolute; right: 30px; top: 30px;
    text-align: right; color: var(--paper); white-space: nowrap;
  }
  .holder-name { font-size: 26px; font-weight: 700; line-height: 1.15; }
  .holder-role { font-size: 13px; font-weight: 700; margin-top: 4px; }
  .holder-address { font-size: 14px; line-height: 1.45; margin-top: 6px; }

  .contacts {
    position: absolute; left: 300px; bottom: 26px;
    list-style: none; color: var(--paper); font-size: 15px; line-height: 1;
    white-space: nowrap;
  }
  .contacts li { display: flex; align-items: center; gap: 12px; margin-top: 9px; }
  .contacts svg { width: 15px; height: 15px; flex: none; }

  .back-brand {
    position: absolute; left: 50%; top: 50%;
    transform: translate(-50%, -50%);
    display: flex; align-items: center; gap: 18px; white-space: nowrap;
  }
  .back-brand .brand-dot { width: 50px; height: 50px; background: var(--paper); }
  .back-brand .brand-name { font-size: 60px; color: var(--paper); }
  .back-url {
    position: absolute; left: 28px; top: 40px;
    writing-mode: vertical-rl;
    color: var(--paper); font-size: 14px; letter-spacing: 4px; white-space: nowrap;
  }
</style>
</head>
<body>
<main class="sheet">

  <section class="card card-front" aria-label="Business card front">
    <svg class="front-shapes" viewBox="0 0 700 400" preserveAspectRatio="none" aria-hidden="true">
      <path d="M120,400 C230,280 370,130 480,0 L500,0 C390,130 250,280 140,400 Z" fill="var(--stripe-grey)"/>
      <path d="M146,400 C256,280 396,130 506,0 L700,0 L700,400 Z" fill="var(--card-blue)"/>
    </svg>

    <div class="brand">
      <span class="brand-dot"></span>
      <span class="brand-name">Moxy Fen</span>
    </div>

    <div class="holder">
      <p class="holder-name">Dara Quell</p>
      <p class="holder-role">CEO, Professional Agile Coach</p>
      <p class="holder-address">PO Box 4410, Fernhill<br>Lower, VIC 3999, Australia</p>
    </div>

    <ul class="contacts">
      <li>
        <svg viewBox="0 0 16 16"><path d="M3 1.5l3 .5 1 3.5-2 1.2a9 9 0 0 0 4.3 4.3l1.2-2 3.5 1 .5 3-2 1.5C7 14 2 9 1.5 3.5z" fill="currentColor"/></svg>
        <span>1300MOXYF</span>
      </li>
      <li>
        <svg viewBox="0 0 16 16"><rect x="4" y="1" width="8" height="14" rx="1.5" fill="none" stroke="currentColor" stroke-width="1.6"/><circle cx="8" cy="12.5" r="0.9" fill="currentColor"/></svg>
        <span>+61 400 712 380</span>
      </li>
      <li>
        <svg viewBox="0 0 16 16"><rect x="1" y="3" width="14" height="10" rx="1" fill="none" stroke="currentColor" stroke-width="1.6"/><path d="M1.5 3.5L8 9l6.5-5.5" fill="none" stroke="currentColor" stroke-width="1.6"/></svg>
        <span>dara@moxy-fen.com.au</span>
      </li>
      <li>
        <svg viewBox="0 0 16 16"><circle cx="8" cy="8" r="6.5" fill="none" stroke="currentColor" stroke-width="1.5"/><ellipse cx="8" cy="8" rx="3" ry="6.5" fill="none" stroke="currentColor" stroke-width="1.2"/><path d="M1.5 8h13" stroke="currentColor" stroke-width="1.2"/></svg>
        <span>www.moxy-fen.com.au</span>
      </li>
    </ul>
  </section>

  <section class="card card-back" aria-label="Business card back">
    <div class="back-brand">
      <span class="brand-dot"></span>
      <span class="brand-name">Moxy Fen</span>
    </div>
    <p class="back-url">www.moxy-fen.com.au</p>
  </section>

</main>
</body>
</html>
```